Health Care Company with Logo Needs Business Cards designed

We are a luxury behavioral health company looking for business cards design we already have a logo and are looking for someone to design a sophisticated luxurious looking business card. Please note that Card design should be captivating just like the logo and also encompass the logo color

Industry/Entity Type

Healthcare

Contact Information for Business Card

Logo,company name, tagline, my name and title, contact details, and physical address

```html
<!DOCTYPE html>
<html lang="en">
<head>
<meta charset="utf-8">
<title>Marlow Behavioral Health – Business Cards</title>
<link href="https://fonts.googleapis.com/css2?family=Roboto+Condensed:wght@700&family=Roboto:ital,wght@0,400;0,500;1,400&display=swap" rel="stylesheet">
<style>
  :root {
    --bg: #2b2b2b;
    --card: #efefef;
    --purple: #7a3486;
    --blue: #0f8fcf;
    --orange: #e28a16;
    --green: #86b12e;
    --ink: #3c3c3c;
    --white: #ffffff;
  }
  * { margin: 0; padding: 0; box-sizing: border-box; }
  html, body { width: 1200px; height: 1138px; overflow: hidden; }
  body { background: var(--bg); position: relative; font-family: "Roboto", sans-serif; }

  .card {
    position: absolute;
    background: linear-gradient(160deg, #f4f4f4 0%, #e9e9e9 60%, #f1f1f1 100%);
    border-radius: 18px;
    overflow: hidden;
  }
  .card--front { left: 274px; top: 186px; width: 623px; height: 376px; }
  .card--back  { left: 276px; top: 608px; width: 618px; height: 374px; }

  .stripe { position: absolute; bottom: 0; height: 7px; }
  .stripe--orange { background: var(--orange); }
  .stripe--blue { background: var(--blue); }
  .stripe--green { background: var(--green); }
  .stripe--purple { background: var(--purple); }

  .brand-name {
    font-family: "Roboto Condensed", sans-serif;
    font-weight: 700;
    color: var(--purple);
    white-space: nowrap;
    line-height: 1;
  }
  .tagline {
    font-family: "Roboto Condensed", sans-serif;
    font-weight: 700;
    color: var(--blue);
    text-transform: uppercase;
    white-space: nowrap;
    line-height: 1;
  }
  .brand-dot { position: absolute; border-radius: 50%; background: var(--purple); }

  /* front */
  .card--front .brand-dot { left: 261px; top: 84px; width: 100px; height: 100px; }
  .card--front .brand-name { position: absolute; left: 0; right: 0; top: 246px; text-align: center; font-size: 37px; }
  .card--front .tagline { position: absolute; left: 0; right: 0; top: 286px; text-align: center; font-size: 12px; letter-spacing: 2.9px; }

  /* back */
  .card--back .brand-dot { left: 34px; top: 52px; width: 88px; height: 88px; }
  .card--back .brand-name { position: absolute; left: 143px; top: 68px; font-size: 45px; letter-spacing: 0.3px; }
  .card--back .tagline { position: absolute; left: 143px; top: 114px; font-size: 14px; letter-spacing: 3.6px; }

  .person { position: absolute; left: 30px; top: 218px; }
  .person__name { font-weight: 500; font-size: 22px; color: var(--purple); letter-spacing: 0.2px; }
  .person__title { font-style: italic; font-size: 15.5px; color: var(--ink); margin-top: 6px; }
  .address { position: absolute; left: 30px; top: 292px; font-size: 15.5px; line-height: 22px; color: var(--ink); }

  .contacts { position: absolute; left: 318px; top: 216px; list-style: none; }
  .contacts li { display: flex; align-items: center; height: 22px; font-size: 15.5px; color: var(--ink); }
  .contacts svg { width: 15px; height: 15px; margin-right: 12px; flex: none; }

  .band {
    position: absolute; left: 248px; right: 0; bottom: 0; height: 46px;
    background: var(--purple);
    clip-path: polygon(28px 0, 100% 0, 100% 100%, 0 100%);
  }
  .band .tagline { position: absolute; left: 42px; top: 18px; font-size: 11px; letter-spacing: 2.6px; color: var(--white); }
</style>
</head>
<body>

<section class="card card--front">
  <div class="brand-dot"></div>
  <h1 class="brand-name">Marlow Behavioral Health</h1>
  <p class="tagline">Dedicated to hope, healing and recovery</p>
  <span class="stripe stripe--orange" style="left:0;width:156px"></span>
  <span class="stripe stripe--blue" style="left:156px;width:156px"></span>
  <span class="stripe stripe--green" style="left:312px;width:156px"></span>
  <span class="stripe stripe--purple" style="left:468px;width:155px"></span>
</section>

<section class="card card--back">
  <div class="brand-dot"></div>
  <h2 class="brand-name">Marlow Behavioral Health</h2>
  <p class="tagline">Dedicated to hope, healing and recovery</p>

  <div class="person">
    <p class="person__name">DANIEL REYES</p>
    <p class="person__title">Managing Director</p>
  </div>
  <p class="address">123, Anywhere ST, Any City,<br>Any Town, US 123456</p>

  <ul class="contacts">
    <li><svg viewBox="0 0 16 16"><path fill="#7a3486" d="M2 6c0-2 2.5-3 6-3s6 1 6 3v1h-3V5.5H5V7H2z"/><rect x="3.5" y="8" width="9" height="6" rx="1" fill="#0f8fcf"/></svg>000-111-0000</li>
    <li><svg viewBox="0 0 16 16"><rect x="1" y="3" width="14" height="10" fill="#0f8fcf"/><path d="M1 3l7 6 7-6M1 13l5-5M15 13l-5-5" stroke="#fff" stroke-width="1.2" fill="none"/></svg>daniel@marlowbehavioral.com</li>
    <li><svg viewBox="0 0 16 16"><circle cx="8" cy="8" r="6.5" fill="#0f8fcf"/><path d="M1.5 8h13M8 1.5c-3 3.5-3 9.5 0 13M8 1.5c3 3.5 3 9.5 0 13" stroke="#fff" stroke-width="0.9" fill="none"/></svg>www.marlowbehavioral.com</li>
  </ul>

  <span class="stripe stripe--orange" style="left:0;width:100px"></span>
  <span class="stripe stripe--blue" style="left:100px;width:100px"></span>
  <span class="stripe stripe--green" style="left:200px;width:60px"></span>
  <div class="band"><p class="tagline">Dedicated to hope, healing and recovery</p></div>
</section>

</body>
</html>
```